Business cards and stationary design

We just completed the design of our new logo and we need to print new business cards and letterhead for our nonprofit. We are looking for a fresh new design that shows off our new logo. On letterhead, we must have a column on the right or left to include our Board of Directors (up to 45 names) (see attachment)

Industry/Entity Type

Non-Profit

Contact Information for Business Card

Standard business card with name, title, Company name, mailing address phone numbers, email address and website. Tagline on back "Bringing the homeless home"

Font styles to use
Sans Serif

Requirements
Must have
• include pertinent information above
• new logo
• fonts compatible with logo
• should use logo colors only
Nice to have
• tag lines

```html
<!DOCTYPE html>
<html lang="en">
<head>
<meta charset="utf-8">
<title>Harbor Home Network – Letterhead</title>
<link href="https://fonts.googleapis.com/css2?family=Questrial&family=Roboto:wght@400;500&display=swap" rel="stylesheet">
<style>
  :root{
    --backdrop:#dedede;
    --paper:#efefef;
    --paper-edge:#e6e6e6;
    --ink:#5a5a5a;
    --ink-dark:#3d3d3d;
    --brand-blue:#1f8fb2;
    --brand-red:#d3282d;
    --signature-blue:#2f6fb5;
    --rule:#8a8a8a;
  }
  *{margin:0;padding:0;box-sizing:border-box}
  html,body{width:1024px;height:1200px;overflow:hidden;background:var(--backdrop)}
  .letterhead{
    position:absolute;left:105px;top:30px;width:814px;height:1140px;
    background:linear-gradient(100deg,var(--paper) 0%,var(--paper-edge) 100%);
    font-family:"Questrial",sans-serif;color:var(--ink);
  }
  .brand{position:absolute;left:80px;top:150px;display:flex;align-items:center;gap:10px}
  .brand-dot{width:14px;height:14px;border-radius:50%;background:var(--brand-red)}
  .brand-name{font-size:19px;letter-spacing:2.5px;color:var(--brand-blue);text-transform:uppercase}
  .contact{position:absolute;left:555px;top:78px;font-family:"Roboto",sans-serif;font-size:11px;line-height:13.5px;color:var(--ink-dark)}
  .contact-org{text-transform:uppercase}
  .contact-lines{margin-top:6px;list-style:none}
  .contact-lines li{display:flex;align-items:center;gap:6px;line-height:14.5px}
  .contact-lines svg{width:10px;height:10px;fill:var(--brand-blue);flex:none}
  .board{position:absolute;left:83px;top:271px;font-family:"Roboto",sans-serif;font-size:11.6px;line-height:16.1px;color:var(--ink-dark)}
  .board-title{font-weight:500;margin-bottom:12px}
  .board-officers{list-style:none;margin-bottom:16px}
  .board-officers b{font-weight:500}
  .board-members{list-style:none}
  .column-rule{position:absolute;left:277px;top:271px;width:1px;height:694px;background:var(--rule)}
  .letter{position:absolute;left:353px;top:270px;width:388px}
  .salutation{font-size:22px;color:var(--ink-dark);margin-bottom:28px}
  .letter p{font-size:11.3px;line-height:16.1px;text-align:justify;margin-bottom:16px}
  .closing{margin-top:20px;font-size:11.3px}
  .signature{display:block;margin-top:8px;width:130px;height:52px;border-radius:26px;
    background:radial-gradient(ellipse at center,rgba(47,111,181,.28),rgba(47,111,181,0) 70%)}
</style>
</head>
<body>
<main class="letterhead">
  <header>
    <div class="brand">
      <span class="brand-dot"></span>
      <span class="brand-name">Harbor Home Network</span>
    </div>
    <address class="contact" style="font-style:normal">
      <div class="contact-org">Harbor Home Network</div>
      <div>412 Alder Bend Road</div>
      <div>Fairview, Oregon 97024</div>
      <ul class="contact-lines">
        <li><svg viewBox="0 0 10 10"><path d="M2 0.5l1.8 2-1 1.2c.6 1.3 1.6 2.3 2.8 2.9l1.2-1 2 1.8-1.1 1.9C4.3 9.2.8 5.7.1 1.6z"/></svg>555 018 2047</li>
        <li><svg viewBox="0 0 10 10"><path d="M0 2h10v6H0z M0 2l5 3.5L10 2" /></svg>office@harborhomenetwork.org</li>
        <li><svg viewBox="0 0 10 10"><circle cx="5" cy="5" r="5"/></svg>www.harborhomenetwork.org</li>
      </ul>
    </address>
  </header>

  <aside class="board">
    <div class="board-title">Board of Directors:</div>
    <ul class="board-officers">
      <li><b>Nolan Ashford</b>, Chair</li>
      <li><b>Reed Calloway</b>, Vice Chair</li>
      <li><b>Ines Marlow</b>, Treasurer</li>
      <li><b>Tara Quill</b>, Secretary</li>
    </ul>
    <ul class="board-members">
      <li>Owen Abbot</li><li>Paul Bexley</li><li>Hugh Branford</li><li>Lena Brisco</li>
      <li>Max Bulwer</li><li>Ray Caddell</li><li>Maren Corliss</li><li>Dean Crayton</li>
      <li>Faye Dunmore</li><li>Rosalie Garnet</li><li>Priya Galvin</li><li>Ada Grover</li>
      <li>Wade Halloran</li><li>Luke Halloran</li><li>Celia Hartwell</li><li>Troy Hobbs</li>
      <li>Glen Holloway</li><li>Vera Hulme</li><li>Joan Irving</li><li>Mira Jessop</li>
      <li>Nadia Lowell</li><li>Clara Mercer</li><li>Felix Northam</li><li>Simon Pardee</li>
      <li>Carl Penrose</li><li>Holly Sterling</li><li>Brent Sowerby</li><li>Ivy Summers</li>
      <li>June Talbot</li><li>Lucy Mayfair</li><li>Greta Thornby</li><li>Samira Valdane</li>
      <li>Norah Whitlock</li><li>Evan Wexford</li><li>Iris Yardley</li><li>Leon Zeller</li>
    </ul>
  </aside>

  <div class="column-rule"></div>

  <article class="letter">
    <div class="salutation">Dear Mr. Carver,</div>
    <p>Lorem ipsum dolor sit amet, consectetur adipiscing elit. Donec orci purus, luctus vitae dignissim eu, iaculis sed purus. Vivamus faucibus, ipsum nec aliquet viverra, leo mauris condimentum ligula, sit amet sagittis enim ligula quis arcu. Nam egestas tortor id nisi porttitor mattis. In tortor ante, ultricies in suscipit a, tempus non massa. Vivamus et auctor mi. Fusce vel massa nulla. Phasellus nec eros mauris, et scelerisque orci.</p>
    <p>Donec malesuada orci vitae nulla accumsan porta a id massa. Quisque accumsan iaculis magna sit amet fringilla. Maecenas consequat, magna eget tincidunt semper, odio nibh rutrum mi, id feugiat ante nisi eu risus. Vestibulum nunc orci, rhoncus a placerat in, ultricies in mi. Cras mattis varius eros, vel fringilla nisi suscipit eget. Quisque scelerisque sagittis nulla at porttitor.</p>
    <p>Sed id augue vitae urna euismod commodo aliquet a quam. Pellentesque arcu velit, cursus et malesuada ut, consequat et diam. Nullam erat sem, rhoncus id ullamcorper vitae, rhoncus et arcu. In ultricies ultricies nulla, ut rutrum nisi iaculis at. Donec eu magna a metus ornare faucibus. Fusce aliquet faucibus ultricies. Morbi semper, est id tincidunt gravida, sem arcu adipiscing lacus, ac bibendum nulla leo eu purus. Quisque nec diam sed risus consectetur a ccumsan quis quis nibh. Vestibulum id purus lorem.</p>
    <p>It is a long established fact that a reader will be distracted by the readable content of a page when looking at its layout. The point of using Lorem Ipsum is that it has a more-or-less normal distribution of letters, as opposed to using 'Content here, content here', making it look like readable English. Many desktop publishing packages</p>
    <div class="closing">Sincerely,</div>
    <span class="signature" role="img" aria-label="Handwritten signature of Daniel Carver in blue ink"></span>
  </article>
</main>
</body>
</html>
```